Business card (AI file uploaded)

We need a business card design that is minimalist using existing logo (attached). Source files must be editable so we can make the same design with other names.

Screenshots included of a design I was working on to give you an idea of the style I would like. Looking for similar modern styles

Thanks

```html
<!DOCTYPE html>
<html lang="en">
<head>
<meta charset="utf-8">
<title>Varenne Law Group – Business Card</title>
<link href="https://fonts.googleapis.com/css2?family=Source+Sans+3:wght@400;600&display=swap" rel="stylesheet">
<style>
  :root {
    --backdrop: #2b2b2b;
    --card-center: #3a3a3a;
    --card-edge: #060606;
    --teal: #16b0a4;
    --white: #ffffff;
    --ink: #0b0b0b;
  }
  * { box-sizing: border-box; margin: 0; padding: 0; }
  html, body {
    width: 1200px; height: 1000px; overflow: hidden;
    background: var(--backdrop);
    font-family: "Source Sans 3", sans-serif;
    color: var(--white);
  }
  .stage { position: relative; width: 1200px; height: 1000px; }

  .card {
    position: absolute;
    background: radial-gradient(ellipse at 45% 40%, var(--card-center) 0%, #141414 55%, var(--card-edge) 100%);
    box-shadow: 0 18px 40px rgba(0,0,0,.55);
    overflow: hidden;
  }

  /* Front */
  .card-front { left: 60px; top: 120px; width: 440px; height: 760px; }
  .front-mark {
    position: absolute; left: 50%; top: 210px; transform: translateX(-50%);
    width: 130px; height: 130px; border: 9px solid var(--white); border-radius: 50%;
  }
  .front-name {
    position: absolute; left: 0; right: 0; top: 410px; text-align: center;
    font-weight: 400; color: var(--white); letter-spacing: 3px; line-height: 1.05;
  }
  .front-name .firm { display: block; font-size: 74px; letter-spacing: 2px; }
  .front-name .firm-sub { display: block; font-size: 44px; letter-spacing: 6px; }
  .practice-band {
    position: absolute; left: 0; right: 0; top: 676px; height: 38px;
    background: var(--teal); color: var(--white);
    font-size: 19px; display: flex; align-items: center; justify-content: center;
  }

  /* Back */
  .card-back { left: 540px; top: 290px; width: 620px; height: 370px; }
  .accent-top {
    position: absolute; left: 60px; top: -20px; width: 24px; height: 120px;
    background: var(--teal); border-radius: 0 0 12px 12px;
  }
  .accent-bottom {
    position: absolute; left: 30px; bottom: -20px; width: 24px; height: 110px;
    background: var(--teal); border-radius: 12px 12px 0 0;
  }
  .person { position: absolute; left: 104px; top: 40px; }
  .person-name { font-size: 40px; font-weight: 600; color: var(--teal); line-height: 1; }
  .person-title { font-size: 19px; margin-top: 6px; }
  .contacts { position: absolute; left: 56px; top: 140px; list-style: none; }
  .contacts li {
    display: flex; align-items: center; gap: 14px;
    font-size: 19px; height: 46px;
  }
  .contacts .icon { width: 30px; height: 30px; flex: none; }
  .contacts .gap { display: inline-block; width: 28px; }
  .back-mark {
    position: absolute; right: 34px; top: 30px;
    display: flex; align-items: center; gap: 8px;
    font-size: 15px; font-weight: 400; color: var(--white); letter-spacing: 1px;
  }
  .back-mark .dot { width: 22px; height: 22px; border: 3px solid var(--white); border-radius: 50%; }
</style>
</head>
<body>
<main class="stage">

  <section class="card card-front" aria-label="Card front">
    <div class="front-mark"></div>
    <h1 class="front-name">
      <span class="firm">VARENNE</span>
      <span class="firm-sub">LAW GROUP PC</span>
    </h1>
    <div class="practice-band">Real Estate | Bankruptcy | Social Security Disability</div>
  </section>

  <section class="card card-back" aria-label="Card back">
    <div class="accent-top"></div>
    <div class="accent-bottom"></div>

    <div class="person">
      <h2 class="person-name">Jordan Varenne</h2>
      <p class="person-title">Attorney At Law</p>
    </div>

    <ul class="contacts">
      <li>
        <svg class="icon" viewBox="0 0 30 30" aria-hidden="true">
          <circle cx="15" cy="15" r="15" fill="var(--teal)"/>
          <path d="M15 7a5.5 5.5 0 0 0-5.5 5.5c0 4 5.5 10 5.5 10s5.5-6 5.5-10A5.5 5.5 0 0 0 15 7z" fill="var(--ink)"/>
          <circle cx="15" cy="12.5" r="2.2" fill="var(--teal)"/>
        </svg>
        <span>418 Meridian Ave., Suite 210, Westbrook, IL 60611</span>
      </li>
      <li>
        <svg class="icon" viewBox="0 0 30 30" aria-hidden="true">
          <circle cx="15" cy="15" r="15" fill="var(--teal)"/>
          <path d="M10 9c1-1 2.2-.8 2.8.2l1.4 2.3c.5.9.2 1.7-.5 2.3l-.8.6c.8 1.7 2 2.9 3.7 3.7l.6-.8c.6-.7 1.4-1 2.3-.5l2.3 1.4c1 .6 1.2 1.8.2 2.8-1.3 1.3-3 1.7-5 .7-3.2-1.6-5.9-4.3-7.5-7.5-1-2-.6-3.7.5-5.2z" fill="var(--ink)"/>
        </svg>
        <span>P: 630.555.0142<span class="gap"></span>F: 630.555.0187</span>
      </li>
      <li>
        <svg class="icon" viewBox="0 0 30 30" aria-hidden="true">
          <circle cx="15" cy="15" r="15" fill="var(--teal)"/>
          <rect x="8" y="10" width="14" height="10" rx="1" fill="none" stroke="var(--ink)" stroke-width="1.8"/>
          <path d="M8.5 10.5 15 15.5l6.5-5" fill="none" stroke="var(--ink)" stroke-width="1.8"/>
        </svg>
        <span>jordan@varennelaw.com</span>
      </li>
    </ul>

    <div class="back-mark"><span class="dot"></span><span>VARENNE</span></div>
  </section>

</main>
</body>
</html>
```